Parcelwise HQ letterhead and envelope

Design a formal (8.5x11) letterhead and envelope for sales outreach and legal matters. Using design input from https://www.parcelwisehq.example/ and the attached documents.

Industry/Entity Type

Software Service

Requirements
Must have
• These 4 hex colors are our official colors:
• #355c98 [blue]
• #1eb1a2 [teal]
• #fdba12 [gold]
• #f1653b [orange]
• So no other colors besides these should be used.

```html
<!DOCTYPE html>
<html lang="en">
<head>
<meta charset="utf-8">
<title>Parcelwise HQ Letterhead</title>
<link rel="stylesheet" href="https://fonts.googleapis.com/css2?family=Open+Sans:wght@300;400;600;700&display=swap">
<style>
:root{
  --blue:#355c98;
  --teal:#1eb1a2;
  --ink:#2b2d31;
  --muted:#5a5f68;
  --rule:#c9ccd2;
  --paper:#ffffff;
  --backdrop:#eceef1;
}
*{margin:0;padding:0;box-sizing:border-box}
html,body{width:1200px;height:784px;overflow:hidden}
body{background:var(--backdrop);font-family:"Open Sans",Arial,sans-serif;color:var(--ink);position:relative}
.letterhead{position:absolute;left:314px;top:22px;width:572px;height:740px;background:var(--paper);box-shadow:0 6px 18px rgba(0,0,0,.12);overflow:hidden}
.edge-band{position:absolute;left:0;top:0;width:90px;height:740px}
.brand{position:absolute;left:56px;top:44px;display:flex;align-items:center;gap:9px}
.brand-mark{width:22px;height:22px;border-radius:50%;background:var(--blue)}
.brand-name{font-size:21px;font-weight:300;color:var(--blue);letter-spacing:.3px;line-height:1}
.contact{position:absolute;right:40px;top:40px;display:flex;gap:12px;font-size:6.5px;color:var(--muted);line-height:1.75}
.contact-list{list-style:none}
.contact-list li{display:flex;align-items:center;gap:4px}
.contact-list svg{width:7px;height:7px;flex:none}
.contact-divider{width:1px;background:var(--rule)}
.office{font-style:normal}
.office-name{font-weight:700;color:var(--blue);font-size:7px}
.letter-body{position:absolute;left:96px;top:128px;width:404px;font-size:8.6px;line-height:1.6;color:var(--ink)}
.salutation{font-weight:700;font-size:10.5px;margin-bottom:12px;color:#111}
.letter-body p{margin-bottom:13px}
.signature{width:84px;height:40px;margin-top:4px;background:linear-gradient(90deg,#f4f5f7,#e9ebee)}
</style>
</head>
<body>
<main class="letterhead">
  <svg class="edge-band" viewBox="0 0 90 740" preserveAspectRatio="none" aria-hidden="true">
    <defs>
      <linearGradient id="swoosh" x1="0" y1="0" x2="0" y2="1">
        <stop offset="0" stop-color="#1eb1a2" stop-opacity="0"/>
        <stop offset=".5" stop-color="#1eb1a2" stop-opacity="1"/>
        <stop offset="1" stop-color="#1eb1a2" stop-opacity=".1"/>
      </linearGradient>
      <linearGradient id="haze" x1="0" y1="0" x2="1" y2="0">
        <stop offset="0" stop-color="#1eb1a2" stop-opacity=".35"/>
        <stop offset="1" stop-color="#1eb1a2" stop-opacity="0"/>
      </linearGradient>
    </defs>
    <path d="M30 0 C40 240 52 480 44 740 H70 C80 480 62 240 40 0 Z" fill="url(#haze)" opacity=".6"/>
    <path d="M31 0 C40 240 50 480 40 740 H44 C55 480 45 240 34 0 Z" fill="url(#swoosh)"/>
    <path d="M0 0 H26 C30 250 34 500 34 740 H0 Z" fill="var(--blue)"/>
  </svg>

  <header>
    <div class="brand">
      <span class="brand-mark"></span>
      <span class="brand-name">Parcelwise HQ</span>
    </div>
    <div class="contact">
      <ul class="contact-list">
        <li><svg viewBox="0 0 10 10"><circle cx="5" cy="5" r="5" fill="var(--blue)"/><path d="M3 2.6l1 .2.4 1.2-.6.5a4 4 0 0 0 1.7 1.7l.5-.6 1.2.4.2 1c-.4.6-1 .8-1.6.5A6 6 0 0 1 2.6 4.2c-.3-.6-.1-1.2.4-1.6z" fill="#fff"/></svg>(555) 014-2290</li>
        <li><svg viewBox="0 0 10 10"><circle cx="5" cy="5" r="5" fill="var(--blue)"/><rect x="2.5" y="3.2" width="5" height="3.6" fill="none" stroke="#fff" stroke-width=".8"/><path d="M2.5 3.3L5 5.2 7.5 3.3" fill="none" stroke="#fff" stroke-width=".8"/></svg>hello@parcelwisehq.example</li>
        <li><svg viewBox="0 0 10 10"><circle cx="5" cy="5" r="5" fill="var(--blue)"/><circle cx="5" cy="5" r="2.6" fill="none" stroke="#fff" stroke-width=".7"/><path d="M2.4 5h5.2M5 2.4v5.2" stroke="#fff" stroke-width=".6"/></svg>www.parcelwisehq.example</li>
      </ul>
      <span class="contact-divider"></span>
      <address class="office">
        <div class="office-name">Parcelwise HQ</div>
        <div>210 Harbor Lane</div>
        <div>Suite 400, NY 10001</div>
      </address>
    </div>
  </header>

  <section class="letter-body">
    <p class="salutation">Dear Mr. John,</p>
    <p>Lorem Ipsum is simply dummy text of the printing and typesetting industry. Lorem Ipsum has been the industry's standard dummy text ever since the 1500s, when an unknown printer took a galley of type and scrambled it to make a type specimen book. It has survived not only five centuries, but also the leap into electronic typesetting, remaining essentially unchanged.</p>
    <p>The standard chunk of Lorem Ipsum used since the 1500s is reproduced below for those interested. Sections 1.10.32 and 1.10.33 from the old sample pages are also reproduced in their exact original form, accompanied by plain English versions from a later printed translation of the same text.</p>
    <p>Lorem Ipsum is simply dummy text of the printing and typesetting industry. Lorem Ipsum has been the industry's standard dummy text ever since the 1500s, when an unknown printer took a galley of type and scrambled it to make a type specimen book. It has survived not only five centuries, but also the leap into electronic typesetting, remaining essentially unchanged. It was popularised in the</p>
    <p>Lorem Ipsum is simply dummy text of the printing and typesetting industry. Lorem Ipsum has been the industry's standard dummy text ever since the 1500s, when an unknown printer took a galley of type and scrambled it to make a type specimen book. It has survived not only five centuries, but also the leap into electronic typesetting, remaining essentially unchanged. It was popularised in the</p>
    <p>Lorem Ipsum is simply dummy text of the printing and typesetting industry. Lorem Ipsum has been the industry's standard dummy text ever since the 1500s, when an unknown printer took a galley of type and scrambled it to make a type specimen book.</p>
    <div class="signature" role="img" aria-label="Handwritten signature of the sender"></div>
  </section>
</main>
</body>
</html>
```